BUSINESS CARD - HALLORAN FIELD SERVICES

I would like to create a business card for my fertilizer spreading business. I would like to incorporate my existing logo and also a description of the services offered. The business card will be given to farmers so must be kept simple but effective. It will also be left in stores so much also be eye catching in order to stand out from other cards.

Target Market(s)

FARMERS

Requirements
Must have
• FRONT OF CARD = EXISTING LOGO + "CUSTOMISED SPREADING" below the logo

REAR Of CARD = SERVICES OFFERED AND CONTACT DETAILS

- Bulk fertilizer including Lime, Gypsum, Manure & Compost
- Granular fertilizer including Single Super, Urea, Gran-am, & Custom Blends
- Modern equipment - Autosteer & Variable Rate Capable
- Friendly & Reliable Service
- Contact Gus: 0417 552 308
Nice to have
• utilize same color scheme as existing logo

```html
<!DOCTYPE html>
<html lang="en">
<head>
<meta charset="utf-8">
<title>Halloran Field Services – Business Card</title>
<link href="https://fonts.googleapis.com/css2?family=Montserrat:wght@400;500;700&display=swap" rel="stylesheet">
<style>
  :root {
    --bg: #ecebe8;
    --card-white: #ffffff;
    --card-grey: #58585a;
    --ink: #5a5a5c;
    --accent: #f7941d;
    --scene-dark: #5f5f61;
    --scene-light: #8a8a8c;
    --light: #ffffff;
  }
  html, body {
    margin: 0;
    width: 1200px;
    height: 1200px;
    overflow: hidden;
    background: var(--bg);
    font-family: "Montserrat", sans-serif;
  }
  .card {
    position: absolute;
    left: 257px;
    width: 686px;
    height: 392px;
    border-radius: 22px;
    overflow: hidden;
    box-shadow: 0 10px 24px rgba(0,0,0,.22);
  }
  .card--front { top: 165px; background: var(--card-white); }
  .card--back  { top: 653px; background: var(--card-grey); color: var(--light); text-align: center; }

  .brand-name {
    position: absolute;
    right: 44px;
    top: 52px;
    margin: 0;
    font-size: 21px;
    font-weight: 700;
    color: var(--ink);
    letter-spacing: .3px;
  }
  .pasture-scene {
    position: absolute;
    left: 0;
    bottom: 0;
    width: 430px;
    height: 215px;
    background: linear-gradient(180deg, var(--scene-light) 0%, var(--scene-dark) 100%);
  }
  .holder {
    position: absolute;
    right: 44px;
    top: 148px;
    text-align: right;
  }
  .holder__name { margin: 0; font-size: 21px; font-weight: 700; color: var(--ink); }
  .holder__role { margin: 2px 0 0; font-size: 15px; color: var(--accent); }
  .contacts {
    list-style: none;
    margin: 14px 0 0;
    padding: 0;
    font-size: 15px;
    color: var(--ink);
    line-height: 20px;
  }
  .contacts li { display: flex; justify-content: flex-end; align-items: center; gap: 10px; }
  .contacts svg { width: 13px; height: 13px; fill: var(--ink); }

  .back-mark {
    display: block;
    margin: 78px auto 0;
    width: 100px;
    height: 100px;
  }
  .back-name {
    margin: 12px 0 0;
    font-size: 26px;
    font-weight: 700;
    letter-spacing: .3px;
  }
  .tagline {
    margin: 6px 0 0;
    font-size: 16px;
    letter-spacing: 2.4px;
    font-weight: 400;
  }
  .services {
    list-style: none;
    margin: 30px 0 0;
    padding: 0;
    font-size: 15px;
    line-height: 19px;
    font-weight: 500;
  }
</style>
</head>
<body>

<section class="card card--front">
  <h1 class="brand-name">HALLORAN FIELD SERVICES</h1>

  <div class="pasture-scene" role="img" aria-label="Grey silhouette of a cow and a sheep standing in grass"></div>

  <div class="holder">
    <p class="holder__name">DANIEL HART</p>
    <p class="holder__role">President</p>
    <ul class="contacts">
      <li>0417 552 308
        <svg viewBox="0 0 24 24"><path d="M6.6 10.8a15.1 15.1 0 0 0 6.6 6.6l2.2-2.2a1 1 0 0 1 1-.25 11.4 11.4 0 0 0 3.6.57 1 1 0 0 1 1 1V20a1 1 0 0 1-1 1A17 17 0 0 1 3 4a1 1 0 0 1 1-1h3.5a1 1 0 0 1 1 1c0 1.25.2 2.45.57 3.6a1 1 0 0 1-.25 1z"/></svg>
      </li>
      <li>info@halloranfield.com
        <svg viewBox="0 0 24 24"><path d="M2 5h20v14H2z"/><path d="M3 6l9 7 9-7" fill="none" stroke="#fff" stroke-width="1.6"/></svg>
      </li>
      <li>www.halloranfield.com
        <svg viewBox="0 0 24 24"><circle cx="12" cy="12" r="10"/><path d="M7 7c3 0 4 2 3 4s-3 1-3 4M15 4c-1 3 2 4 4 5M14 14c2 0 3 2 2 5" fill="none" stroke="#fff" stroke-width="1.6"/></svg>
      </li>
    </ul>
  </div>
</section>

<section class="card card--back">
  <svg class="back-mark" viewBox="0 0 100 100" aria-hidden="true">
    <circle cx="50" cy="50" r="46" fill="none" stroke="#e0e0e0" stroke-width="4"/>
  </svg>
  <h2 class="back-name">HALLORAN FIELD SERVICES</h2>
  <p class="tagline">CUSTOMISED SPREADING</p>
  <ul class="services">
    <li>Bulk fertilizer including Lime, Gypsum, Manure &amp; Compost</li>
    <li>Granular fertilizer including Single Super, Urea, Gran-am, &amp; Custom Blends</li>
    <li>Modern equipment - Autosteer &amp; Variable Rate Capable</li>
    <li>Friendly &amp; Reliable Service</li>
  </ul>
</section>

</body>
</html>
```